DESIGN OF STATIONERY - TORVALE MED

WE WORK IN THE FIELD OF HEALTH (IMAGING: MRI - CT ETC.).
WE WOULD LIKE TO CREATE THE ENTIRE STATIONERY DESIGN : LETTERHEAD, BUSINESS CARD, CALENDAR, INVOICES, CD HOLDER, ETC.

Target Market(s)

PERSONS UNDERTAKING HEALTH EXAMINATIONS

```html
<!DOCTYPE html>
<html lang="en">
<head>
<meta charset="utf-8">
<title>Torvale Med – Business Card</title>
<link rel="stylesheet" href="https://fonts.googleapis.com/css2?family=Montserrat:wght@400;500;600;700&display=swap">
<style>
  :root {
    --bg: #e9ecef;
    --paper: #ffffff;
    --paper-shade: #eef0f2;
    --blue-deep: #1d7fc1;
    --blue-light: #33a2d8;
    --teal: #2bb5a8;
    --text-light: #ffffff;
  }
  * { box-sizing: border-box; margin: 0; padding: 0; }
  html, body {
    width: 1200px; height: 900px; overflow: hidden;
    background: var(--bg);
    font-family: "Montserrat", sans-serif;
  }
  .business-card {
    position: absolute; left: 100px; top: 165px;
    width: 1000px; height: 571px;
    background: linear-gradient(160deg, var(--paper-shade), var(--paper) 60%);
    box-shadow: 0 10px 30px rgba(0,0,0,0.18);
    overflow: hidden;
  }
  .card-art { position: absolute; inset: 0; }
  .brand-name {
    position: absolute; right: 70px; top: 170px;
    font-weight: 600; font-size: 52px; letter-spacing: 1px;
    color: var(--teal);
  }
  .holder {
    position: absolute; left: 64px; top: 275px;
    color: var(--text-light);
  }
  .holder-name {
    font-weight: 600; font-size: 28px; letter-spacing: 1.5px; text-transform: uppercase;
  }
  .holder-title { font-weight: 500; font-size: 21px; margin-top: 2px; }
  .contact-list { list-style: none; margin-top: 18px; }
  .contact-list li {
    display: flex; align-items: center; gap: 12px;
    font-size: 19px; font-weight: 400; line-height: 30px;
  }
  .contact-icon { width: 18px; height: 18px; flex: none; fill: var(--text-light); }
  .office-address {
    position: absolute; right: 60px; bottom: 34px;
    text-align: right; color: var(--text-light);
    font-size: 21px; font-weight: 400; line-height: 30px;
  }
</style>
</head>
<body>
  <div class="business-card">
    <svg class="card-art" viewBox="0 0 1000 571" preserveAspectRatio="none" aria-hidden="true">
      <defs>
        <linearGradient id="bandBlue" x1="0" y1="0" x2="1" y2="0.4">
          <stop offset="0" stop-color="#1a76b8"/>
          <stop offset="0.6" stop-color="#33a2d8"/>
          <stop offset="1" stop-color="#1d84c4"/>
        </linearGradient>
        <linearGradient id="accentFade" x1="0" y1="0" x2="1" y2="0">
          <stop offset="0.3" stop-color="#2bb5a8" stop-opacity="0"/>
          <stop offset="0.6" stop-color="#2bb5a8" stop-opacity="1"/>
        </linearGradient>
      </defs>
      <path class="card-band" d="M0,232 C380,250 720,300 1000,372 L1000,571 L0,571 Z" fill="url(#bandBlue)"/>
      <path class="card-accent" d="M0,226 C380,244 720,294 1000,366" fill="none" stroke="url(#accentFade)" stroke-width="6"/>
    </svg>

    <div class="brand-name">TORVALE MED</div>

    <div class="holder">
      <p class="holder-name">Alden R. Whitcombe</p>
      <p class="holder-title">President</p>
      <ul class="contact-list">
        <li>
          <svg class="contact-icon" viewBox="0 0 24 24"><path d="M6.6 10.8a15.1 15.1 0 0 0 6.6 6.6l2.2-2.2c.3-.3.7-.4 1-.2 1.1.4 2.3.6 3.6.6.6 0 1 .4 1 1V20c0 .6-.4 1-1 1A17 17 0 0 1 3 4c0-.6.4-1 1-1h3.5c.6 0 1 .4 1 1 0 1.3.2 2.5.6 3.6.1.3 0 .7-.2 1z"/></svg>
          07700 900 415
        </li>
        <li>
          <svg class="contact-icon" viewBox="0 0 24 24"><path d="M2 5h20v14H2z M3.5 6.5 12 13l8.5-6.5" fill="none" stroke="#fff" stroke-width="2"/></svg>
          info@torvalemed.com
        </li>
        <li>
          <svg class="contact-icon" viewBox="0 0 24 24"><circle cx="12" cy="12" r="9" fill="none" stroke="#fff" stroke-width="2"/><path d="M3 12h18M12 3c3 3 3 15 0 18M12 3c-3 3-3 15 0 18" fill="none" stroke="#fff" stroke-width="1.6"/></svg>
          www.torvalemed.com
        </li>
      </ul>
    </div>

    <address class="office-address" style="font-style:normal">
      Torvale-Med-R<br>
      2nd Floor 18 Calder Row<br>
      Glasgow G3 7QL
    </address>
  </div>
</body>
</html>
```